Unique Business Card Design

Unique Business Card design for our orthotic and prosthetic company. Our logo is on our website, color is light blue. Unique shape (artificial leg shaped, vertical, etc..) preferred. Logo, business name, individual name and basic demographics needed.

Industry/Entity Type

Business

Contact Information for Business Card

Logo, Industry, Phone # Logo, "Prosthetic & Orthotic Services" Place to add individual name and contact info

Colors
cee9f5

Requirements
Must have
• The icon must be there, placement of "Prosthetic & Orthotic Services" can be moved
Nice to have
• Like the mix of light blue, and a little darker blue. One design included the icons from my website which was a nice touch

```html
<!DOCTYPE html>
<html lang="en">
<head>
<meta charset="utf-8">
<title>Limbworks Inc. Business Card</title>
<link href="https://fonts.googleapis.com/css2?family=Open+Sans:wght@400;600;700&display=swap" rel="stylesheet">
<style>
  :root {
    --brand-blue: #1560ac;
    --brand-blue-soft: #3a80c4;
    --ink-grey: #555555;
    --edge-grey: #4d4d4d;
    --paper: #ffffff;
    --backdrop: #4a4a4a;
  }
  * { margin: 0; padding: 0; box-sizing: border-box; }
  html, body { width: 1105px; height: 1200px; overflow: hidden; }
  body {
    background: var(--backdrop);
    font-family: "Open Sans", Arial, sans-serif;
    position: relative;
  }
  .card {
    position: absolute;
    left: 193px;
    width: 721px;
    height: 410px;
    overflow: hidden;
  }
  .card-front { top: 167px; background: var(--paper); }
  .card-back { top: 623px; background: var(--brand-blue); }

  /* front: brand lockup */
  .brand-lockup { position: absolute; left: 40px; top: 156px; display: flex; align-items: center; gap: 18px; }
  .brand-dot { width: 80px; height: 80px; border-radius: 50%; background: var(--brand-blue); }
  .brand-text { display: flex; flex-direction: column; }
  .brand-name { color: var(--brand-blue); font-size: 27px; font-weight: 600; line-height: 1; letter-spacing: 0.2px; }
  .brand-rule { height: 2px; background: var(--brand-blue); margin: 5px 0 4px; }
  .brand-tagline { color: var(--brand-blue); font-size: 13px; font-weight: 600; }

  .divider { position: absolute; left: 365px; top: 81px; width: 1px; height: 235px; background: #c9c9c9; }

  .contact { position: absolute; left: 392px; top: 74px; color: var(--ink-grey); }
  .person-name { color: var(--brand-blue); font-size: 26px; font-weight: 600; line-height: 1.1; }
  .person-title { color: var(--brand-blue); font-size: 17px; font-weight: 600; margin-top: 2px; }
  .address { font-size: 18.5px; line-height: 27px; margin-top: 10px; }
  .contact-list { list-style: none; margin-top: 8px; }
  .contact-list li { display: flex; align-items: center; gap: 10px; font-size: 18.5px; line-height: 27.5px; }
  .contact-list svg { width: 18px; height: 18px; flex: none; fill: var(--brand-blue); }

  .front-footer { position: absolute; left: 0; bottom: 0; width: 721px; height: 44px; }
  .web-front { position: absolute; left: 450px; bottom: 9px; color: #fff; font-size: 19px; letter-spacing: 0.8px; }

  /* back */
  .back-disc { position: absolute; left: 10px; top: 6px; width: 400px; height: 400px; border-radius: 50%; background: var(--brand-blue-soft); opacity: 0.75; }
  .back-lockup { position: absolute; left: 400px; top: 284px; width: 290px; color: #fff; }
  .back-name { font-size: 31px; font-weight: 600; line-height: 1; white-space: nowrap; }
  .back-rule { height: 4px; background: #fff; margin: 8px 0 6px; }
  .back-tagline { font-size: 16px; font-weight: 600; text-align: center; }
  .back-web { font-size: 17px; letter-spacing: 2px; margin-top: 4px; text-align: center; }
</style>
</head>
<body>
  <section class="card card-front">
    <div class="brand-lockup">
      <div class="brand-dot"></div>
      <div class="brand-text">
        <span class="brand-name">LIMBWORKS INC.</span>
        <span class="brand-rule"></span>
        <span class="brand-tagline">Prosthetic &amp; Orthotic Services</span>
      </div>
    </div>

    <div class="divider"></div>

    <div class="contact">
      <h1 class="person-name">MIRELA ASHFORD</h1>
      <p class="person-title">CO LPO</p>
      <p class="address">2150 Alder Row<br>Westbrook, NY 10455</p>
      <ul class="contact-list">
        <li><svg viewBox="0 0 24 24"><path d="M6.6 10.8a15 15 0 0 0 6.6 6.6l2.2-2.2a1 1 0 0 1 1-.25 11.4 11.4 0 0 0 3.6.57 1 1 0 0 1 1 1V20a1 1 0 0 1-1 1A17 17 0 0 1 3 4a1 1 0 0 1 1-1h3.5a1 1 0 0 1 1 1c0 1.25.2 2.45.57 3.57a1 1 0 0 1-.25 1z"/></svg>555.210.4800</li>
        <li><svg viewBox="0 0 24 24"><path d="M7 1h10a2 2 0 0 1 2 2v18a2 2 0 0 1-2 2H7a2 2 0 0 1-2-2V3a2 2 0 0 1 2-2zm0 3v14h10V4zm5 15.5a1 1 0 1 0 0 2 1 1 0 0 0 0-2z"/></svg>555.210.4815</li>
        <li><svg viewBox="0 0 24 24"><path d="M6 2h12v5H6zM3 8h18a2 2 0 0 1 2 2v7h-4v-3H5v3H1v-7a2 2 0 0 1 2-2zm3 7h12v7H6z"/></svg>555-3107264</li>
        <li><svg viewBox="0 0 24 24"><path d="M2 5h20v14H2zm2 2v.5l8 5 8-5V7zm0 2.8V17h16V9.8l-8 5z"/></svg>mashford@limbworksinc.com</li>
      </ul>
    </div>

    <svg class="front-footer" viewBox="0 0 721 44" aria-hidden="true">
      <rect x="0" y="32" width="390" height="12" fill="var(--edge-grey)"/>
      <polygon points="403,0 721,0 721,44 380,44" fill="var(--brand-blue)"/>
    </svg>
    <span class="web-front">www.limbworksinc.com</span>
  </section>

  <section class="card card-back">
    <div class="back-disc"></div>
    <div class="back-lockup">
      <div class="back-name">LIMBWORKS INC.</div>
      <div class="back-rule"></div>
      <div class="back-tagline">Prosthetic &amp; Orthotic Services</div>
      <div class="back-web">www.limbworksinc.com</div>
    </div>
  </section>
</body>
</html>
```